A website for a Maltese Law Firm

Our law firm needs a website to further its business. The site should have a simple yet effective design. We would need the following sections: About us, Practice Areas, About Malta, Contact. These should be further split as follows:

About us: Our firm, Our values, What others say, Offices

Practice Areas: Crimimal, Citizenship & Residence, Sovereign Patron Pathway, Criminal Defence, Civil Litigation, Arbitration and ADR, Commercial and Corporate, Media Law.

About Malta: just one section.

Contact: Just one section

We would also need a news feed at the front of the site to include latest news regarding our cases.

At the bottom we need a section for our Terms and a Privacy Statement.

Our logo is being attached.

Target Market(s)

All clients looking for legal assistance in Malta

Industry/Entity Type

Legal

Coding

Coded - Design and coding required

Number of Pages Required

1 page

Requirements
Must have
• It must be simple yet striking.

```html
<!DOCTYPE html>
<html lang="en">
<head>
<meta charset="utf-8">
<title>Galea &amp; Borg Advocates</title>
<link rel="stylesheet" href="https://fonts.googleapis.com/css2?family=Cinzel:wght@400;600&family=Lato:wght@400;700&display=swap">
<style>
:root{
  --ink:#1b1b1b;
  --night:#141414;
  --footer:#1c1c1c;
  --base:#111111;
  --paper:#ebebeb;
  --mist:#e4e4e4;
  --card:#e8e8e8;
  --white:#ffffff;
  --text:#2a2a2a;
  --muted:#bbbbbb;
  --cream:#f3e8d2;
  --rule:#9a9a9a;
}
*{box-sizing:border-box;margin:0;padding:0}
html,body{width:1200px;height:2590px;overflow:hidden}
body{font-family:'Lato',sans-serif;color:var(--text);background:var(--white)}
.heading{font-family:'Cinzel',serif;font-weight:400;letter-spacing:1px}

/* header */
.site-header{height:98px;background:var(--ink);position:relative;border-bottom:4px solid #3a3a3a}
.brand{position:absolute;left:98px;top:28px;font-family:'Cinzel',serif;font-size:26px;color:var(--white);letter-spacing:1px;white-space:nowrap}
.call{position:absolute;right:98px;top:14px;display:flex;align-items:center;gap:12px;font-family:'Cinzel',serif;font-size:19px;color:var(--white)}
.main-nav{position:absolute;right:98px;top:64px;display:flex;gap:22px;font-family:'Cinzel',serif;font-size:14px;color:var(--white)}
.main-nav .sep{color:#888}

/* hero */
.hero{height:515px;position:relative;background:linear-gradient(100deg,#5a3a1c 0%,#8a6232 18%,#3a2a1c 42%,#2b2b2e 62%,#c9c4ba 85%,#6f6a62 100%)}
.hero-photo{position:absolute;inset:0}
.hero-title{position:absolute;left:0;right:0;top:200px;text-align:center;font-family:'Cinzel',serif;font-weight:400;font-size:32px;line-height:46px;color:var(--cream);letter-spacing:1px}
.btn-consult{position:absolute;left:492px;top:306px;width:214px;height:37px;background:var(--white);color:#111;font-size:15px;font-weight:700;display:flex;align-items:center;justify-content:center}
.hero-arrow{position:absolute;top:336px}
.hero-arrow.left{left:41px}.hero-arrow.right{left:1121px}

/* about */
.about{height:402px;background:var(--paper);position:relative}
.portrait-frame{position:absolute;left:98px;top:52px;width:294px;height:297px;background:#d8d8d8;padding:16px}
.portrait{width:100%;height:100%;background:linear-gradient(160deg,#9a9a9a,#6a6a6a 60%,#3a3a3a)}
.about-body{position:absolute;left:440px;top:42px;width:662px}
.section-title{font-size:33px;color:#161616}
.title-rule{height:2px;background:linear-gradient(90deg,#555 0 40%,#c4c4c4 40% 100%);margin:6px 0 16px}
.about-body .title-rule{width:490px}
.copy{font-size:13px;line-height:24.5px}
.bullets{display:flex;gap:40px;margin:16px 0 20px;font-size:14px;font-weight:700;color:#111}
.bullets li{list-style:none;display:flex;align-items:center;gap:14px}
.bullets li::before{content:"";width:9px;height:9px;border-radius:50%;background:#555}
.btn-dark{display:inline-flex;align-items:center;justify-content:center;width:110px;height:34px;background:#0d0d0d;color:var(--white);font-size:13px}

/* practice */
.practice{height:501px;background:var(--white);position:relative}
.centered-title{text-align:center;padding-top:40px}
.centered-title .title-rule{width:350px;margin:6px auto 0;background:linear-gradient(90deg,#c4c4c4 0 28%,#555 28% 72%,#c4c4c4 72% 100%)}
.practice-intro{text-align:center;font-size:13px;margin-top:16px}
.practice-cards{position:absolute;left:98px;top:159px;display:flex;gap:38px}
.practice-card{width:309px;height:297px;background:var(--card);border-bottom:4px solid #1a1a1a;position:relative;text-align:center}
.practice-img{height:142px}
.icon-badge{position:absolute;left:128px;top:118px;width:52px;height:52px;border-radius:50%;background:var(--white);display:flex;align-items:center;justify-content:center}
.practice-name{font-family:'Cinzel',serif;font-weight:400;font-size:18px;margin-top:36px;color:#1a1a1a}
.practice-text{font-size:13px;line-height:19px;margin:14px 28px 0;color:#444}
.slide-arrow{position:absolute;top:294px}
.slide-arrow.left{left:52px}.slide-arrow.right{left:1128px}

/* malta */
.malta{height:314px;background:var(--night);position:relative;color:var(--white)}
.malta-body{position:absolute;left:98px;top:40px;width:610px}
.malta .section-title{color:var(--white)}
.malta .title-rule{width:230px;background:linear-gradient(90deg,#bbb 0 40%,#444 40% 100%)}
.malta .copy{color:#e0e0e0}
.btn-outline{display:inline-flex;align-items:center;justify-content:center;width:112px;height:34px;border:1px solid #ccc;color:var(--white);font-size:13px;margin-top:16px}
.malta-photo{position:absolute;left:775px;top:59px;width:327px;height:190px;border:2px solid #dfe6f2;background:linear-gradient(180deg,#2a3f78 0%,#4a5a90 35%,#c27a3a 62%,#7a3f25 75%,#2a3f78 100%)}

/* news */
.news{height:463px;background:var(--mist);position:relative}
.news .centered-title{padding-top:34px}
.news .title-rule{width:220px}
.news-cards{position:absolute;left:98px;top:116px;display:flex;gap:33px}
.news-card{width:309px}
.news-img{height:195px;position:relative}
.news-date{position:absolute;right:14px;top:12px;background:#0e0e0e;color:var(--white);font-size:12px;padding:5px 14px}
.news-title{font-size:15px;font-weight:700;color:#111;margin-top:14px}
.news-text{font-size:13px;line-height:20px;margin-top:14px;color:#333}

/* footer */
.site-footer{height:297px;background:var(--footer);position:relative;color:#d6d6d6}
.footer-col{position:absolute;top:38px}
.footer-col h3{font-family:'Cinzel',serif;font-weight:400;font-size:18px;letter-spacing:1px;color:#e4e4e4;padding-bottom:6px;border-bottom:1px solid #4a4a4a;margin-bottom:14px}
.quick-links{left:98px;width:140px}
.quick-links li{list-style:none;font-size:13px;line-height:27.5px}
.quick-links li::before{content:"›";margin-right:10px;color:#aaa}
.contact-col{left:290px;width:200px}
.contact-line{display:flex;gap:12px;font-size:13px;line-height:19px;margin-bottom:12px}
.contact-line svg{flex:none;margin-top:3px}
.map-col{left:568px;width:262px}
.map{width:262px;height:137px;border:3px solid #f0f0f0;background:linear-gradient(135deg,#ecebe4,#d9dfe6)}
.divider{position:absolute;top:38px;width:1px;height:200px;background:#383838}
.footer-brand{position:absolute;left:893px;top:120px;width:220px;text-align:center;font-family:'Cinzel',serif;font-size:16px;line-height:20px;color:var(--white);white-space:nowrap;padding-bottom:4px;border-bottom:1px solid #8a8a8a}
.social{position:absolute;left:940px;top:164px;display:flex;gap:8px}
.social span{width:24px;height:24px;border-radius:50%;background:#5a5a5a}
.copyright{position:absolute;left:0;right:0;bottom:0;height:43px;background:var(--base);color:#cfcfcf;font-size:13px;display:flex;align-items:center;justify-content:center}
</style>
</head>
<body>

<header class="site-header">
  <div class="brand">Galea &amp; Borg Advocates</div>
  <div class="call">
    <svg width="26" height="26" viewBox="0 0 26 26"><circle cx="13" cy="13" r="12" fill="none" stroke="#fff" stroke-width="1.6"/><path d="M9 7.5l2.2 2.6-1.3 1.6c.8 1.8 2.2 3.2 4 4l1.6-1.3 2.6 2.2-1.4 1.9c-4.2-.4-8.2-4.4-8.6-8.6z" fill="#fff"/></svg>
    <span>Call: (356) 2100-4471</span>
  </div>
  <nav class="main-nav">
    <span>Home</span><span class="sep">|</span><span>About Us</span><span class="sep">|</span><span>Practice Areas</span><span class="sep">|</span><span>About Malta</span><span class="sep">|</span><span>Contact Us</span>
  </nav>
</header>

<section class="hero">
  <div class="hero-photo" role="img" aria-label="Lawyer in a suit signing documents at a desk in front of law book shelves"></div>
  <h1 class="hero-title">The greatest And Strongest<br>Firm You Can Trust</h1>
  <a class="btn-consult">Request A Free Consult</a>
  <svg class="hero-arrow left" width="38" height="38" viewBox="0 0 38 38"><circle cx="19" cy="19" r="17" fill="none" stroke="#fff" stroke-width="1.6"/><path d="M22 12l-7 7 7 7" fill="none" stroke="#fff" stroke-width="1.8"/></svg>
  <svg class="hero-arrow right" width="38" height="38" viewBox="0 0 38 38"><circle cx="19" cy="19" r="17" fill="none" stroke="#fff" stroke-width="1.6"/><path d="M16 12l7 7-7 7" fill="none" stroke="#fff" stroke-width="1.8"/></svg>
</section>

<section class="about">
  <div class="portrait-frame"><div class="portrait" role="img" aria-label="Portrait photo of a firm partner in a suit"></div></div>
  <div class="about-body">
    <h2 class="heading section-title">About Galea &amp; Borg</h2>
    <div class="title-rule"></div>
    <p class="copy">Lorem ipsum dolor sit amet, consectetuer adipiscing elit, sed diam nonummy nibh euismod tincidunt ut laoreet dolore magna aliquam erat volutpat. Ut wisi enim ad minim veniam, quis nostrud exerci tation ullamcorper suscipit lobortis nisl ut aliquip ex ea commodo consequat. Duis autem vel eum iriure dolor in hendrerit in vulputate velit esse molestie consequat, vel illum dolore eu feugiat nulla facilisis at vero eros et accumsan et iusto odio dignissim qui blandit praesent luptatum zzril delenit augue duis dolore te feugait nulla facilisi.</p>
    <ul class="bullets"><li>Our Firms</li><li>Our Values</li></ul>
    <a class="btn-dark">Read More</a>
  </div>
</section>

<section class="practice">
  <div class="centered-title">
    <h2 class="heading section-title">Our Practice Areas</h2>
    <div class="title-rule"></div>
  </div>
  <p class="practice-intro">Lorem ipsum dolor sit amet, consectetur adipisicing elit. Obcaecati laborum ipsa, a voluptates libero possimus sapiente.</p>
  <svg class="slide-arrow left" width="18" height="36" viewBox="0 0 18 36"><path d="M16 2L2 18l14 16" fill="none" stroke="#666" stroke-width="1.6"/></svg>
  <svg class="slide-arrow right" width="18" height="36" viewBox="0 0 18 36"><path d="M2 2l14 16L2 34" fill="none" stroke="#666" stroke-width="1.6"/></svg>
  <div class="practice-cards">
    <article class="practice-card">
      <div class="practice-img" role="img" aria-label="Law books with a gavel and scales of justice" style="background:linear-gradient(180deg,#5a3a22,#b88a4e 55%,#3a2414)"></div>
      <div class="icon-badge"><svg width="28" height="24" viewBox="0 0 28 24"><circle cx="8" cy="15" r="6" fill="none" stroke="#222" stroke-width="2.4"/><circle cx="20" cy="15" r="6" fill="none" stroke="#222" stroke-width="2.4"/><path d="M11 6h6" stroke="#222" stroke-width="2.4"/><circle cx="10" cy="6" r="2" fill="#222"/><circle cx="18" cy="6" r="2" fill="#222"/></svg></div>
      <h3 class="practice-name">Crminal Law</h3>
      <p class="practice-text">Sed ut perspiciatis unde omnis iste natus error sit voluptatem accusantium omnis unde doloremque laudantium</p>
    </article>
    <article class="practice-card">
      <div class="practice-img" role="img" aria-label="Passports resting on a world map" style="background:linear-gradient(160deg,#d9d2c0,#8a2a24 55%,#2a2430)"></div>
      <div class="icon-badge"><svg width="26" height="24" viewBox="0 0 26 24"><path d="M13 2L1 12h3v10h7v-6h4v6h7V12h3z" fill="#222"/></svg></div>
      <h3 class="practice-name">Citizenship And Residence</h3>
      <p class="practice-text">Sed ut perspiciatis unde omnis iste natus error sit voluptatem accusantium omnis unde doloremque laudantium</p>
    </article>
    <article class="practice-card">
      <div class="practice-img" role="img" aria-label="Columned court building against a blue sky" style="background:linear-gradient(180deg,#2a5aa8,#8fa8c8 45%,#d8d2c4)"></div>
      <div class="icon-badge"><svg width="26" height="24" viewBox="0 0 26 24"><path d="M13 1L1 7v2h24V7z" fill="#222"/><rect x="3" y="10" width="3" height="9" fill="#222"/><rect x="9" y="10" width="3" height="9" fill="#222"/><rect x="15" y="10" width="3" height="9" fill="#222"/><rect x="21" y="10" width="3" height="9" fill="#222"/><rect x="1" y="20" width="24" height="3" fill="#222"/></svg></div>
      <h3 class="practice-name">Civil Litigation</h3>
      <p class="practice-text">Sed ut perspiciatis unde omnis iste natus error sit voluptatem accusantium omnis unde doloremque laudantium</p>
    </article>
  </div>
</section>

<section class="malta">
  <div class="malta-body">
    <h2 class="heading section-title">About Malta</h2>
    <div class="title-rule"></div>
    <p class="copy">Lorem ipsum dolor sit amet, consectetur adipisicing elit, sed do eiusmod tempor incididunt ut labore et dolore magna aliqua. Ut enim ad minim veniam, quis nostrud exercitation ullamco laboris nisi ut aliquip ex ea commodo consequat. Duis aute irure dolor in reprehenderit in voluptate velit esse cillum dolore eu fugiat nulla pariatur. Excepteur sint occaecat cupidatat non proident, sunt in culpa qui officia deserunt mollit anim id est laborum.</p>
    <a class="btn-outline">Read More</a>
  </div>
  <div class="malta-photo" role="img" aria-label="Valletta skyline lit up at dusk across the harbour"></div>
</section>

<section class="news">
  <div class="centered-title">
    <h2 class="heading section-title">Latest News</h2>
    <div class="title-rule"></div>
  </div>
  <div class="news-cards">
    <article class="news-card">
      <div class="news-img" role="img" aria-label="Lawyer signing papers at a desk with a gavel" style="background:linear-gradient(160deg,#3a3a3a,#8a8680 50%,#4a3020)"><span class="news-date">08, June</span></div>
      <h3 class="news-title">We denounce with righteous indignation and.</h3>
      <p class="news-text">At vero eos et accusamus et iusto odio dignissimos ducimus qui blanditiis praesentium voluptatum deleniti atque corrupti quos dolores et.</p>
    </article>
    <article class="news-card">
      <div class="news-img" role="img" aria-label="Brass scales of justice on a table" style="background:linear-gradient(160deg,#e0c8a8,#a8682e 50%,#5a2e14)"><span class="news-date">08, June</span></div>
      <h3 class="news-title">We denounce with righteous indignation and.</h3>
      <p class="news-text">At vero eos et accusamus et iusto odio dignissimos ducimus qui blanditiis praesentium voluptatum deleniti atque corrupti quos dolores et.</p>
    </article>
    <article class="news-card">
      <div class="news-img" role="img" aria-label="Close view of stone columns" style="background:linear-gradient(90deg,#f2f0ec,#b8b4ac 40%,#e8e6e0 60%,#6a6660)"><span class="news-date">08, June</span></div>
      <h3 class="news-title">We denounce with righteous indignation and.</h3>
      <p class="news-text">At vero eos et accusamus et iusto odio dignissimos ducimus qui blanditiis praesentium voluptatum deleniti atque corrupti quos dolores et.</p>
    </article>
  </div>
</section>

<footer class="site-footer">
  <div class="footer-col quick-links">
    <h3>Quick Links</h3>
    <ul><li>Home</li><li>About Us</li><li>Practice Areas</li><li>About Malta</li><li>Contact Us</li></ul>
  </div>
  <div class="divider" style="left:262px"></div>
  <div class="footer-col contact-col">
    <h3>Contact Detail</h3>
    <div class="contact-line"><svg width="10" height="14" viewBox="0 0 10 14"><path d="M5 0a5 5 0 015 5c0 3.5-5 9-5 9S0 8.5 0 5a5 5 0 015-5z" fill="#ddd"/><circle cx="5" cy="5" r="1.8" fill="#1c1c1c"/></svg><span>12/4, Harbour Lane, Valletta<br>88, Olive Grove Street, Mosta</span></div>
    <div class="contact-line"><svg width="12" height="12" viewBox="0 0 12 12"><path d="M2 1l2 2.4-1 1.4c.8 1.6 2 2.8 3.6 3.6l1.4-1L10.4 9 9 11C4.8 10.6 1.4 7.2 1 3z" fill="#ddd"/></svg><span>(356) 2100-4471</span></div>
    <div class="contact-line"><svg width="12" height="12" viewBox="0 0 12 12"><rect x="3" y="0" width="6" height="4" fill="#ddd"/><rect x="0" y="4" width="12" height="5" fill="#ddd"/><rect x="3" y="8" width="6" height="4" fill="#ddd"/></svg><span>(356) 2100-4472</span></div>
    <div class="contact-line"><svg width="12" height="10" viewBox="0 0 12 10"><rect x="0" y="0" width="12" height="10" fill="#ddd"/><path d="M0 0l6 5 6-5" fill="none" stroke="#1c1c1c" stroke-width="1.2"/></svg><span>info@galeaborglaw.com</span></div>
  </div>
  <div class="divider" style="left:530px"></div>
  <div class="footer-col map-col">
    <h3>Location Map</h3>
    <div class="map" role="img" aria-label="Street map showing the office location"></div>
  </div>
  <div class="divider" style="left:866px"></div>
  <div class="footer-brand">Galea &amp; Borg Advocates</div>
  <div class="social"><span></span><span></span><span></span><span></span></div>
  <div class="copyright">Copyright © 2016 - Galea &amp; Borg Advocates, All Rights Reserved.</div>
</footer>

</body>
</html>
```